Syndicated consumer advocate seeks cool and creative web design

I'd like to collaborate with a web designer-artist to help me reimagine my web presence, Danmorwicks.com. I publish my syndicated news articles on this site and collect email addresses for my weekly email newsletter. I want to maintain the current minimalist look and feel -- simple, uncluttered, intuitive -- while evolving it to the next level of functionality.

I take my inspiration from several nonprofit organizations and news sites. Those include 714, the Prairie Ledger, and CivoWatch. I want to use those sites as my leitmotif for the new theme, while also adopting some of their features.

Here's more about me: https://danmorwicks.com/about-daniel-morwick/

NOTE: Please be as creative as you want with your suggestions. I can handle it! I love outside-the-box thinking.

Target Market(s)

North American consumers.

Industry/Entity Type

News

Font styles to use
Sans Serif

Colors

Designer to choose only greyscale colors for use in the design.

Requirements
Must have
• The new theme should be visually appealing and very fast.

I'm looking for the ability to determine a "lead" story and control the content of other story boxes on the front page.

I don't mind using a starter theme such as Groundwork (I'm using that for the current version). However, I would prefer to not use an out-of-the-box news theme and simply modify it. I would like the coding to be watertight and error-free and hope to achieve console scores in the 90s.
Nice to have
• I like harmony, balance and Zen. I would like all the elements, including text, ads and social icons to look as if they are built with purpose and thought. It might be necessary to re-imagine or re-interpret the logo.
Should not have
• Please, no sliders. No bulky coding. No animations. No bright colors.

```html
<!DOCTYPE html>
<html lang="en">
<head>
<meta charset="utf-8">
<title>Daniel Morwick</title>
<link rel="stylesheet" href="https://fonts.googleapis.com/css2?family=Questrial&family=Montserrat:wght@400;500;600;700&display=swap">
<style>
:root{
  --ink:#111;
  --black:#000;
  --white:#fff;
  --paper:#f4f4f4;
  --slate:#4a4a4a;
  --bar:#555;
  --rule:#888;
  --photo-a:#9a9a9a;
  --photo-b:#6f6f6f;
  --photo-c:#c4c4c4;
}
*{box-sizing:border-box;margin:0;padding:0}
html,body{width:1200px;height:3684px;overflow:hidden}
body{font-family:"Montserrat",sans-serif;color:var(--ink);background:var(--white);position:relative}
.wrap{position:absolute;left:172px;width:855px}
.display{font-family:"Questrial",sans-serif;font-weight:400}
.photo{background:linear-gradient(135deg,var(--photo-c),var(--photo-a) 55%,var(--photo-b))}
.by{font-size:12px;margin-top:8px}

/* header */
.site-header{position:absolute;top:0;left:0;width:1200px;height:109px}
.brand{position:absolute;left:172px;top:30px}
.brand-name{font-family:"Questrial",sans-serif;font-size:31px;font-weight:400;line-height:40px}
.social{position:absolute;left:597px;top:44px;display:flex;gap:16px}
.social span{width:26px;height:26px;border-radius:50%;background:var(--black);display:block}
.search{position:absolute;left:764px;top:33px;width:263px;height:49px;border:2px solid var(--black);display:flex}
.search span{flex:1;font-size:14px;color:#555;padding:14px 10px}
.search button{width:45px;height:45px;background:var(--black);border:0;display:flex;align-items:center;justify-content:center}

.main-nav{position:absolute;top:109px;left:0;width:1200px;height:63px;background:var(--black)}
.main-nav a{position:absolute;top:0;height:63px;line-height:63px;color:var(--white);font-size:15px;font-weight:500;text-decoration:none;letter-spacing:.3px}
.main-nav a.current{background:var(--bar);padding:0 36px;left:172px}

/* hero */
.hero{top:222px;height:400px}
.lead{position:absolute;left:0;top:0;width:469px}
.lead .photo{height:293px}
.lead h2{font-family:"Questrial",sans-serif;font-size:17px;font-weight:400;line-height:27px;text-transform:uppercase;margin-top:15px}
.side{position:absolute;left:486px;width:369px;display:flex;gap:12px}
.side .photo{width:190px;height:179px;flex:none}
.side h3{font-family:"Questrial",sans-serif;font-size:16px;font-weight:400;line-height:27px;text-transform:uppercase;margin-top:12px}
.side p{font-size:11.5px;line-height:21px;text-align:justify;margin-top:12px}

/* recent */
.recent-band{position:absolute;top:684px;left:0;width:1200px;height:861px;background:var(--paper)}
.section-title{font-size:30px;text-transform:uppercase}
.recent{top:742px}
.card{position:absolute;width:279px}
.bar{height:43px;background:var(--bar);color:var(--white);font-family:"Questrial",sans-serif;font-size:21px;line-height:43px;padding-left:15px;text-transform:uppercase}
.card .photo{height:168px;margin-top:8px}
.card h3{font-family:"Questrial",sans-serif;font-size:16.5px;font-weight:400;line-height:24px;margin-top:14px}
.latest{position:absolute;left:587px;top:70px;width:268px;height:647px;background:var(--white)}
.latest ul{list-style:none;padding:24px 14px 0 12px}
.latest li{font-family:"Questrial",sans-serif;font-size:12px;line-height:24px;padding-left:15px;position:relative}
.latest li::before{content:"";position:absolute;left:0;top:8px;border-left:5px solid var(--black);border-top:4px solid transparent;border-bottom:4px solid transparent}

/* about */
.about-band{position:absolute;top:1545px;left:0;width:1200px;height:829px;background:var(--slate);color:var(--white)}
.about{top:81px}
.about-photo{float:left;width:532px;height:353px;border:2px solid var(--white);margin:0 36px 22px 0}
.about h2{font-size:30px;line-height:38px;margin-bottom:14px}
.about p{font-size:11.5px;line-height:22.5px;text-align:justify;font-weight:500}
.about p+p{margin-top:20px}
.about h2.wide{clear:both;margin:20px 0 12px}

/* featured */
.featured{top:2458px}
.featured .section-title{text-align:center}
.feature{position:absolute;top:83px;width:279px}
.feature .photo{height:262px}
.feature h3{font-family:"Questrial",sans-serif;font-size:16px;font-weight:400;line-height:24px;margin-top:14px}
.feature p{font-size:10.5px;line-height:18px;margin-top:10px}
.brief{position:absolute;top:512px;width:285px;display:flex;gap:12px}
.brief .photo{width:141px;height:111px;flex:none}
.brief h4{font-family:"Questrial",sans-serif;font-size:13px;font-weight:400;line-height:20px;margin-top:4px}
.brief p{font-size:10.5px;line-height:18px;text-align:justify;margin-top:8px}

/* footer */
.site-footer{position:absolute;top:3165px;left:0;width:1200px;height:519px;background:var(--black);color:var(--white)}
.help{position:absolute;top:56px;width:1200px;text-align:center;font-size:15px;font-weight:700;letter-spacing:-.3px}
.appeal{position:absolute;top:122px;width:300px}
.appeal h4{font-size:14px;font-weight:700;letter-spacing:-.3px}
.appeal p{font-size:11px;line-height:18px;margin-top:16px}
.appeal span{display:inline-block;margin-top:12px;background:var(--white);color:var(--ink);font-size:12px;padding:7px 12px}
.divider{position:absolute;height:1px;background:var(--rule)}
.underwriters{position:absolute;top:317px;width:1200px;text-align:center;font-size:15px;font-weight:700;letter-spacing:-.3px}
.partners{position:absolute;top:360px;left:200px;width:800px;display:flex;justify-content:space-between;align-items:center}
.partners span{font-size:13px;font-weight:600}
.copyright{position:absolute;top:468px;width:1200px;text-align:center;font-size:15px;letter-spacing:.3px}
</style>
</head>
<body>

<header class="site-header">
  <div class="brand"><span class="brand-name">Daniel Morwick</span></div>
  <div class="social" aria-label="Social links"><span></span><span></span><span></span><span></span></div>
  <div class="search">
    <span>Search</span>
    <button aria-label="Search">
      <svg width="18" height="18" viewBox="0 0 18 18"><circle cx="7.5" cy="7.5" r="5.5" fill="none" stroke="#fff" stroke-width="2.4"/><line x1="11.5" y1="11.5" x2="16.5" y2="16.5" stroke="#fff" stroke-width="2.6"/></svg>
    </button>
  </div>
</header>

<nav class="main-nav">
  <a class="current" href="#">HOME</a>
  <a href="#" style="left:315px">ABOUT</a>
  <a href="#" style="left:436px">NEWSLETTER</a>
  <a href="#" style="left:611px">FEATURES</a>
  <a href="#" style="left:767px">TOPICS</a>
  <a href="#" style="left:894px">MORWICK.ORG</a>
</nav>

<section class="wrap hero">
  <article class="lead">
    <div class="photo" role="img" aria-label="Airport terminal hallway with gate signs and travelers"></div>
    <h2>I paid twice for my airline ticket — can I get one refunded?</h2>
    <p class="by">By Andrews</p>
  </article>
  <article class="side" style="top:0">
    <div class="photo" role="img" aria-label="Businessman walking through an airport with a suitcase"></div>
    <div><h3>Possible travel restrictions</h3><p>After a mixup with her cruise line, Rena Talbot pays for her airline tickets twice. Is there...</p></div>
  </article>
  <article class="side" style="top:196px">
    <div class="photo" role="img" aria-label="Traveler in a hat sitting by an airport window with her phone"></div>
    <div><h3>Wanted: long-term accommodations</h3><p>After a mixup with her cruise line, Rena Talbot pays for her airline tickets twice. Is there...</p></div>
  </article>
</section>

<div class="recent-band"></div>
<section class="wrap recent">
  <h2 class="section-title display">Recent Stories</h2>
  <article class="card" style="left:0;top:70px">
    <div class="bar">Travel</div>
    <div class="photo" role="img" aria-label="Couple resting by a mountain lake"></div>
    <h3>Travelers rethink their travel rewards cards after the pandemic</h3>
    <p class="by">By Alexander</p>
  </article>
  <article class="card" style="left:293px;top:70px">
    <div class="bar">Covid</div>
    <div class="photo" role="img" aria-label="Tourist in a sun hat overlooking a historic city"></div>
    <h3>How do I prove I’ve had a COVID-19 shot?</h3>
    <p class="by">By Alexander</p>
  </article>
  <article class="card" style="left:0;top:399px">
    <div class="bar">Travel</div>
    <div class="photo" role="img" aria-label="Family silhouettes with luggage at an airport window at sunset"></div>
    <h3>Here are the most common travel problems — and solutions</h3>
    <p class="by">By Alexander</p>
  </article>
  <article class="card" style="left:293px;top:399px">
    <div class="bar">Ticket</div>
    <div class="photo" role="img" aria-label="Backpack and map on a rocky mountain top"></div>
    <h3>I paid twice for my tickets. Can I get a Loftway Airlines</h3>
    <p class="by">By Alexander</p>
  </article>
  <aside class="latest">
    <div class="bar">Latest Stories</div>
    <ul>
      <li>I paid twice for my airline ticket — can I get one refunded?</li>
      <li>Wanted: Long-term accommodations for workcation travelers</li>
      <li>Possible travel restrictions have travelers asking: What if?</li>
      <li>A Bulkway Club laptop computer problem: Where’d it go?</li>
      <li>This RailIsle pass refund request has gone off the rails</li>
      <li>What to do about travelers who refuse to wear a mask</li>
      <li>Traveling without a vaccine? Here’s what you need to know</li>
      <li>My Aeroval ticket is not refundable. Why not?</li>
      <li>How do you get rid of a fraudulent transaction on PayNest?</li>
      <li>Here’s how to get dual citizenship and a second passport</li>
    </ul>
  </aside>
</section>

<div class="about-band">
  <section class="wrap about">
    <div class="about-photo photo" role="img" aria-label="Daniel Morwick speaking at a conference podium"></div>
    <h2 class="display">About Daniel Morwick</h2>
    <p>The Sharpest Traveler’s Handbook (And Save Time, Money and Hassle) (Geo Atlas) is the book you’ll want to take on your next trip. It’s full of actionable advice you won’t find anywhere else. It also answers the most common and most perplexing travel questions. The Sharpest Traveler’s Handbook shows you how to save time and money and prevent hassles. Morwick shares his favorite shortcuts and bargain tips. He reveals which ones are too good to be true. Plus, he explains how to avoid travel irritants such as onerous contracts or aggressive timeshare salespeople.</p>
    <p>Fleeced: How to Save Your Money and Find Better Service in a World of Schemes, Swindles, and Shady Deals (Harlow Press) is the ultimate guide for consumers. Once upon a time, store prices were simple and fair, businesses stood behind their products with guarantees free of fine print and loopholes. Companies genuinely cared about their valued customers. But those days are long gone. In this exposé of corporate America, Morwick pulls the curtains back on the broken relationship between American consumers and businesses. He explains how companies came to believe that fooling their customers was a viable, and profitable, business plan.</p>
    <h2 class="display wide">Daniel Morwick’s advocacy</h2>
    <p>Morwick Advocacy is a 501 (c)(3) nonprofit organization that empowers people to solve their problems and helps those who can’t. Morwick.org helps readers through direct advocacy, journalism on an ad-free website and maintaining the largest database of executive contact information on the internet.</p>
  </section>
</div>

<section class="wrap featured">
  <h2 class="section-title display">Featured Stories</h2>
  <article class="feature" style="left:0">
    <div class="photo" role="img" aria-label="Traveler with a backpack overlooking old town rooftops at sunset"></div>
    <h3>Possible travel restrictions have travelers asking: What if?</h3>
    <p>Stephen Walsh asks his travel agent for a RailIsle pass refund. But six months later.</p>
  </article>
  <article class="feature" style="left:288px">
    <div class="photo" role="img" aria-label="Smiling couple walking down a city street"></div>
    <h3>A Bulkway Club laptop computer problem: Where’d it go?</h3>
    <p>Stephen Walsh asks his travel agent for a RailIsle pass refund. But six months later.</p>
  </article>
  <article class="feature" style="left:576px">
    <div class="photo" role="img" aria-label="City skyline at dusk with snowy hills and traffic trails"></div>
    <h3>This RailIsle pass refund request has gone off the rails</h3>
    <p>Stephen Walsh asks his travel agent for a RailIsle pass refund. But six months later.</p>
  </article>
  <article class="brief" style="left:0">
    <div class="photo" role="img" aria-label="Businessman at a desk with a microphone"></div>
    <div><h4>I want to cancel my Telvora service.</h4><p>At vero eos et ac cusamus et iusto odio dignissimos.</p></div>
  </article>
  <article class="brief" style="left:293px">
    <div class="photo" role="img" aria-label="Hands holding a question mark sign among microphones"></div>
    <div><h4>I want to cancel my Telvora service.</h4><p>At vero eos et ac cusamus et iusto odio dignissimos.</p></div>
  </article>
  <article class="brief" style="left:582px">
    <div class="photo" role="img" aria-label="Woman on a sofa using a tablet"></div>
    <div><h4>I want to cancel my Telvora service.</h4><p>At vero eos et ac cusamus et iusto odio dignissimos.</p></div>
  </article>
</section>

<footer class="site-footer">
  <div class="help">HELP US HELP YOU</div>
  <div class="appeal" style="left:285px">
    <h4>I’m a consumer</h4>
    <p>Consumer advocacy is difficult and dangerous work. We rely on individual supporters to cover the sizeable costs of publishing a daily news site.</p>
    <span>Donate</span>
  </div>
  <div class="appeal" style="left:625px">
    <h4>I’m with a company</h4>
    <p>Morwick Advocacy works with forward-looking companies who want to be associated with our advocacy mission. Find out how to get involved.</p>
    <span>More</span>
  </div>
  <div class="divider" style="top:303px;left:259px;width:681px"></div>
  <div class="underwriters">MORWICK ADVOCACY UNDERWRITERS</div>
  <div class="partners">
    <span>Roamwise</span><span>Covera Travel</span><span>Voyanta</span><span>Tripsafe</span><span>Keyline Rentals</span><span>Linkwave</span><span>Drivemark</span>
  </div>
  <div class="divider" style="top:427px;left:172px;width:855px"></div>
  <div class="copyright">Copyrights @ 2021 Danmorwicks. All Rights Reserved.</div>
</footer>

</body>
</html>
```